Business card design for Virtual Assistance company

I need a business card designed for my virtual assistance company. We are a small company who services primarily C-level executive clients. The card needs to be double sided with the following contact information on the back:
Melissa Thornbury
Owner/CEO
info@rkpadvisory.net
www.rkpadvisory.net
555.302.9817

The front side should just have the company name incorporated: "RKP Advisory" and "virtual assistance"

The card should be simplistic, but eye catching and should speak to high level executives. Our primary focus areas consist of executive assistance and government contracting.

Target Market(s)

CEOs and executives

Contact Information for Business Card

see project description. phone, email, website.

Colors

Designer to choose only greyscale colors for use in the design.

```html
<!DOCTYPE html>
<html lang="en">
<head>
<meta charset="utf-8">
<title>RKP Advisory – Business Card</title>
<link rel="stylesheet" href="https://fonts.googleapis.com/css2?family=Cinzel:wght@600&family=Poppins:wght@400&display=swap">
<style>
  :root {
    --stage: #2a2a2a;
    --card: #1d1d1d;
    --card-back: #121212;
    --accent: #d6d6d6;
    --accent-ink: #1d1d1d;
    --white: #ffffff;
    --grey: #b9b9b9;
    --rule: #6c6c6c;
  }
  * { margin: 0; padding: 0; box-sizing: border-box; }
  html, body { width: 1200px; height: 1108px; overflow: hidden; }
  body { background: var(--stage); position: relative; font-family: "Poppins", sans-serif; }

  .card {
    position: absolute;
    width: 420px; height: 660px;
    border-radius: 22px;
    overflow: hidden;
    box-shadow: 0 14px 40px rgba(0,0,0,.45);
  }
  .card--front { left: 150px; top: 220px; background: var(--card); }
  .card--back { left: 640px; top: 240px; background: var(--card-back); }

  .brand {
    position: absolute; top: 120px; left: 0; right: 0;
    text-align: center;
    font-family: "Cinzel", serif; font-weight: 600;
    font-size: 50px; line-height: 1.1; color: var(--accent);
  }
  .tagline {
    position: absolute; top: 250px; left: 40px; right: 40px;
    display: flex; align-items: center; gap: 14px;
    color: var(--grey); font-size: 15px; letter-spacing: 4px;
    text-transform: uppercase; white-space: nowrap;
  }
  .tagline::before, .tagline::after { content: ""; flex: 1; height: 2px; background: var(--grey); }

  .holder { position: absolute; top: 410px; left: 0; right: 0; text-align: center; }
  .holder__name {
    font-family: "Cinzel", serif; font-weight: 600;
    font-size: 26px; color: var(--accent); letter-spacing: 1px;
  }
  .holder__role { font-size: 19px; color: var(--white); margin-top: 2px; }

  .icon-row {
    position: absolute; top: 498px; left: 40px; right: 40px;
    display: flex; align-items: center; gap: 8px;
  }
  .icon-row::before, .icon-row::after { content: ""; flex: 1; height: 1px; background: var(--rule); }
  .icon { width: 30px; height: 30px; border-radius: 5px; background: var(--accent); display: flex; align-items: center; justify-content: center; }
  .icon svg { width: 20px; height: 20px; }

  .contact {
    position: absolute; top: 550px; left: 0; right: 0;
    text-align: center; list-style: none;
    color: var(--white); font-size: 18px; line-height: 1.45;
  }

  .back-pattern {
    position: absolute; inset: 0;
    background: linear-gradient(225deg, #5a5a5a 0%, #2c2c2c 35%, #151515 70%, #0c0c0c 100%);
  }
  .back-mark {
    position: absolute; left: 230px; top: 480px;
    font-family: "Cinzel", serif; font-weight: 600;
    font-size: 22px; color: var(--accent); white-space: nowrap;
  }
</style>
</head>
<body>
  <section class="card card--front">
    <div class="brand">RKP<br>Advisory</div>
    <div class="tagline">Virtual Assistance</div>

    <div class="holder">
      <div class="holder__name">MELISSA THORNBURY</div>
      <div class="holder__role">Owner/CEO</div>
    </div>

    <div class="icon-row">
      <span class="icon" aria-label="Phone">
        <svg viewBox="0 0 20 20"><path d="M5 3l3 3-2 2c1 2 3 4 5 5l2-2 3 3-2 3C8 16 4 12 3 5z" fill="var(--accent-ink)"/></svg>
      </span>
      <span class="icon" aria-label="Email">
        <svg viewBox="0 0 20 20"><rect x="3" y="5" width="14" height="10" fill="none" stroke="var(--accent-ink)" stroke-width="1.6"/><path d="M3 5l7 6 7-6" fill="none" stroke="var(--accent-ink)" stroke-width="1.6"/></svg>
      </span>
      <span class="icon" aria-label="Website">
        <svg viewBox="0 0 20 20"><circle cx="10" cy="10" r="7" fill="none" stroke="var(--accent-ink)" stroke-width="1.6"/><ellipse cx="10" cy="10" rx="3" ry="7" fill="none" stroke="var(--accent-ink)" stroke-width="1.3"/><path d="M3 10h14" stroke="var(--accent-ink)" stroke-width="1.3"/></svg>
      </span>
    </div>

    <ul class="contact">
      <li>555.302.9817</li>
      <li>info@rkpadvisory.net</li>
      <li>www.rkpadvisory.net</li>
    </ul>
  </section>

  <section class="card card--back">
    <div class="back-pattern" role="img" aria-label="Repeating tonal brand-name pattern in glossy black and grey"></div>
    <div class="back-mark">RKP Advisory</div>
  </section>
</body>
</html>
```